NEW Wordpress Website Design for a Dynamic Long Term Healthcare Company in Hawaii

I would like a new website design for my current company, Marlow Health Collective, which has two different brands - Marlow Homecare and Marlow Senior Living. You can see the current website at www.marlowhealth-example.com. The website should be built using Wordpress Software and the Framewise theme. The website should have a local Hawaii island/tropical feel, but look professional for healthcare. I'm looking for something fresh, and want the designer to select colors, styles, etc.

In the Header, on all pages, I would like a menu that includes Home Care, Senior Living, Rates, and About Us.
Under each of the Header Menu Titles, I would like these drop downs included:
Home Care (drop down pages)- Nurse Aide Care, 24-Hour Home Care, Skilled Nursing, Lifestyle Aide, Hospice at Home, Bathing & Meal Service.
Senior Living (drop down pages) - Long-Term Stay, Short-Term Stay.
Rates (drop down page) - Rates.
About Us (drop down pages) - Our Mission, Ohana Talk, About Dana Marlow.

In the footer, on all pages, you should include the address: 248 Pueo Lane, Suite 310, Honolulu, HI 96817. Phone number: 808-555-0172
The footer should also include buttons for a page called Learn, Caregiver Jobs, and each of the service page links to include: Nurse Aide Care, 24-Hour Home Care, Skilled Nursing, Lifestyle Aide, Hospice at Home, Bathing & Meal Service.
Please don't take the current website and redesign a few aspects. I'm looking for a completely different look and feel.

Target Market(s)

40-80 year olds

Industry/Entity Type

Long Term Healthcare

Coding

Coded - Design and coding required

Requirements
Should not have
• Our existing website as a template. We are looking for a complete redesign. Thank you.

```html
<!DOCTYPE html>
<html lang="en">
<head>
<meta charset="utf-8">
<title>Marlow Health Collective</title>
<link href="https://fonts.googleapis.com/css2?family=Marcellus&family=Roboto:wght@400;500;700&display=swap" rel="stylesheet">
<style>
:root{
  --teal:#1fa39a;
  --teal-dark:#16897f;
  --green:#3aae7c;
  --nav-active:#2aa85c;
  --ink:#2b2b2b;
  --body:#444;
  --cream:#f8efe3;
  --panel:#f3ebe4;
  --grad-start:#f3f56e;
  --grad-mid:#9ee28a;
  --grad-end:#1ea69d;
  --white:#fff;
}
*{box-sizing:border-box;margin:0;padding:0}
html,body{width:1200px;height:2887px;overflow:hidden}
body{position:relative;background:var(--white);font-family:'Roboto',sans-serif;color:var(--body)}
.abs{position:absolute}
.serif{font-family:'Marcellus',serif}
.btn{position:absolute;display:flex;align-items:center;justify-content:center;color:var(--white);font-weight:700;font-size:15px;border-radius:6px;background:linear-gradient(90deg,var(--grad-start),var(--grad-mid) 40%,var(--grad-end));text-shadow:0 0 2px rgba(0,0,0,.15)}
/* header */
.brand{position:absolute;left:110px;top:40px;width:130px;display:flex;flex-direction:column;align-items:center;gap:8px;font-family:'Marcellus',serif;font-size:19px;line-height:1.1;color:var(--ink);text-align:center}
.brand-mark{width:30px;height:30px;background:var(--ink);border-radius:6px}
.nav{position:absolute;top:47px;left:366px;display:flex;gap:24px;font-size:15px;color:var(--ink)}
.nav span{display:flex;align-items:center;gap:5px}
.nav .active{color:var(--nav-active);font-weight:500}
.caret{width:0;height:0;border-left:4px solid transparent;border-right:4px solid transparent;border-top:5px solid var(--ink)}
.sub-brand{position:absolute;top:30px;width:100px;display:flex;flex-direction:column;align-items:center;gap:6px;font-family:'Marcellus',serif;font-size:15px;line-height:1.1;text-align:center;color:var(--teal-dark)}
.sub-brand i{width:22px;height:22px;border-radius:50%;display:block}
/* hero */
.hero{position:absolute;left:0;top:100px;width:1200px;height:457px;overflow:hidden;background:var(--cream)}
.hero-photo{position:absolute;inset:0;background:linear-gradient(105deg,#139fb2 0%,#4cc3c8 20%,#a9dfd6 30%,#eadcc6 40%,#f8efe3 55%)}
.hero-title{position:absolute;left:560px;width:548px;top:80px;text-align:center;font-size:42px;line-height:44px;color:var(--ink)}
.hero-text{position:absolute;left:560px;width:548px;top:190px;text-align:center;font-size:15px;line-height:30px;color:var(--ink)}
/* sections */
.sec-title{position:absolute;font-size:41px;color:var(--teal);letter-spacing:.5px;line-height:1}
.sec-sub{position:absolute;font-size:24px;color:var(--green);line-height:1}
.sec-text{position:absolute;font-size:15.5px;line-height:28.5px;color:var(--body)}
.flower{position:absolute;width:60px;height:44px;border-radius:50% 45% 50% 40%;background:radial-gradient(circle,#e9f27a,#5ccf93 60%,#2ab09e)}
.heart{position:absolute}
/* form */
.consult-title{position:absolute;left:0;width:1200px;top:1592px;text-align:center;font-size:42px;line-height:51px;color:var(--teal)}
.panel{position:absolute;left:112px;top:1732px;width:976px;height:591px;background:var(--panel);border-radius:18px}
.field{position:absolute;height:52px;background:var(--white);border-radius:4px;box-shadow:0 1px 3px rgba(0,0,0,.08);padding-left:34px;display:flex;align-items:center;font-size:15.5px;color:var(--ink)}
.consent{position:absolute;left:247px;top:2187px;font-size:14.5px;color:#666}
/* footer */
.waves{position:absolute;left:0;top:2400px;width:1200px;height:170px;background:linear-gradient(180deg,rgba(255,255,255,0) 0%,#a9dde4 35%,#8fd0da 55%,rgba(230,247,250,.6) 100%)}
.footer-bg{position:absolute;left:0;top:2560px;width:1200px;height:327px;background:linear-gradient(180deg,#fff 0%,#eef9fa 45%,#d4f1f4 100%)}
.f-head{position:absolute;font-family:'Marcellus',serif;font-size:16.5px;color:var(--teal);letter-spacing:.5px}
.f-list{position:absolute;font-size:15.5px;line-height:26px;color:var(--ink);list-style:none}
.contact{position:absolute;left:849px;font-size:15.5px;line-height:27px;color:var(--ink);display:flex;gap:12px}
.contact svg{flex:none;margin-top:5px}
.social{position:absolute;top:2782px;width:31px;height:31px;border:1.5px solid var(--green);border-radius:50%}
.social::after{content:"";position:absolute;left:10px;top:10px;width:8px;height:8px;border-radius:50%;background:var(--green)}
.copy{position:absolute;left:0;width:1200px;top:2839px;text-align:center;font-size:16px;color:var(--ink)}
</style>
</head>
<body>

<header>
  <div class="brand"><span class="brand-mark"></span>Marlow Health<br>Collective</div>
  <nav class="nav">
    <span class="active">Home</span>
    <span>Home Care <i class="caret"></i></span>
    <span>Senior Living <i class="caret"></i></span>
    <span>Rates <i class="caret"></i></span>
    <span>About Us <i class="caret"></i></span>
  </nav>
  <div class="sub-brand" style="left:882px"><i style="background:#ef8a78"></i>Marlow Homecare</div>
  <div class="sub-brand" style="left:988px"><i style="background:#5aa9a2"></i>Marlow Senior Living</div>
</header>

<section class="hero">
  <div class="hero-photo" role="img" aria-label="Turquoise ocean water washing onto a sandy beach"></div>
  <svg class="abs" style="left:0;top:0" width="1200" height="60" viewBox="0 0 1200 60" preserveAspectRatio="none">
    <path d="M0 0 H1200 V55 C1120 20 1020 5 900 10 C700 20 500 48 300 42 C170 38 80 20 0 12 Z" fill="#fff"/>
  </svg>
  <h1 class="hero-title serif" style="font-weight:400">Hawaii's Choice<br>Homecare &amp; Senior Living</h1>
  <p class="hero-text">Marlow Homecare provides a variety of professional in-home health care<br>services throughout the entire island of Oahu.<br>Marlow Senior Living, a beautiful Adult Residential Care Home, is located<br>on the windward side of Oahu in Kailua.</p>
  <a class="btn" style="left:775px;top:356px;width:128px;height:42px">Learn More</a>
</section>

<section class="homecare">
  <h2 class="sec-title serif" style="left:113px;top:650px;font-weight:400">HOMECARE</h2>
  <div class="flower" style="left:383px;top:645px" role="img" aria-label="Hibiscus flower ornament"></div>
  <p class="sec-sub serif" style="left:112px;top:702px">Professional Care In Your Home</p>
  <p class="sec-text" style="left:113px;top:748px;width:480px">Marlow Homecare understands that every person's care journey is unique. We tailor our in-home services to meet the diverse nurturing experience of professional quality care and safety within the comfort and convenience of your own home.</p>
  <a class="btn" style="left:113px;top:886px;width:231px;height:43px">Schedule Care Assessment</a>
  <svg class="heart" style="left:657px;top:644px" width="431" height="364" viewBox="0 0 100 90" preserveAspectRatio="none" role="img" aria-label="Three women knitting together on a sofa in a bright living room">
    <defs><linearGradient id="g1" x1="0" y1="0" x2="1" y2="1"><stop offset="0" stop-color="#d9dc8a"/><stop offset=".5" stop-color="#b98a5c"/><stop offset="1" stop-color="#6b4a30"/></linearGradient></defs>
    <path d="M50 88 C20 60 0 45 0 25 C0 10 12 0 25 0 C37 0 46 8 50 18 C54 8 63 0 75 0 C88 0 100 10 100 25 C100 45 80 60 50 88Z" fill="url(#g1)"/>
  </svg>
  <div class="abs" style="left:670px;top:905px;width:159px;height:187px;border-radius:45%;background:linear-gradient(135deg,#eef47e,#7fdc9a 55%,#36b8a0);opacity:.75" role="img" aria-label="Tribal sea turtle illustration"></div>
</section>

<section class="senior">
  <svg class="heart" style="left:112px;top:1168px" width="431" height="361" viewBox="0 0 100 90" preserveAspectRatio="none" role="img" aria-label="Caregiver in teal scrubs helping a senior man in a bedroom">
    <defs><linearGradient id="g2" x1="0" y1="0" x2="1" y2="1"><stop offset="0" stop-color="#e0dc78"/><stop offset=".55" stop-color="#c9c46a"/><stop offset="1" stop-color="#3a97c4"/></linearGradient></defs>
    <path d="M50 88 C20 60 0 45 0 25 C0 10 12 0 25 0 C37 0 46 8 50 18 C54 8 63 0 75 0 C88 0 100 10 100 25 C100 45 80 60 50 88Z" fill="url(#g2)"/>
  </svg>
  <h2 class="sec-title serif" style="left:618px;top:1175px;font-weight:400">SENIOR LIVING</h2>
  <div class="flower" style="left:933px;top:1170px" role="img" aria-label="Hibiscus flower ornament"></div>
  <p class="sec-sub serif" style="left:618px;top:1227px">Trusted Care In Our Home</p>
  <p class="sec-text" style="left:619px;top:1272px;width:480px">Marlow Senior Living creates a warm, supportive, and enriching care home environment where seniors can thrive in their golden years. We provide residential care that promotes well-being, connection, and dignity of each individual.</p>
  <a class="btn" style="left:619px;top:1410px;width:149px;height:43px">Schedule Tour</a>
</section>

<section class="consult">
  <h2 class="consult-title serif" style="font-weight:400">SCHEDULE A COMPLIMENTARY<br>CARE CONSULTATION</h2>
  <div class="flower" style="left:838px;top:1640px" role="img" aria-label="Hibiscus flower ornament"></div>
  <div class="panel"></div>
  <div class="field" style="left:243px;top:1781px;width:347px">Name</div>
  <div class="field" style="left:607px;top:1781px;width:347px">Phone</div>
  <div class="field" style="left:243px;top:1849px;width:711px">Email</div>
  <div class="field" style="left:243px;top:1917px;width:711px">How can we help?</div>
  <div class="field" style="left:243px;top:1986px;width:711px">Questions / Comments</div>
  <div class="field" style="left:243px;top:2054px;width:711px">How did you hear about us?</div>
  <div class="field" style="left:243px;top:2123px;width:711px">May we email you about this?</div>
  <p class="consent">You agree to receive future emails and understand you may opt-out at any time</p>
  <a class="btn" style="left:243px;top:2228px;width:711px;height:42px">Submit Now</a>
</section>

<footer>
  <div class="footer-bg"></div>
  <div class="waves" role="img" aria-label="Watercolor ocean wave pattern"></div>
  <a class="btn" style="left:115px;top:2614px;width:148px;height:43px">Learn</a>
  <a class="btn" style="left:115px;top:2675px;width:148px;height:42px">Caregiver Jobs</a>

  <h3 class="f-head" style="left:386px;top:2619px;font-weight:400">QUICK LINKS</h3>
  <ul class="f-list" style="left:387px;top:2660px">
    <li>Nurse Aide Care</li><li>24-Hour Home Care</li><li>Skilled Nursing</li>
  </ul>
  <h3 class="f-head" style="left:595px;top:2619px;font-weight:400">OTHER LINKS</h3>
  <ul class="f-list" style="left:595px;top:2660px">
    <li>Lifestyle Aide</li><li>Hospice at Home</li><li>Bathing &amp; Meal Service</li>
  </ul>
  <h3 class="f-head" style="left:849px;top:2619px;font-weight:400">CONTACT US</h3>
  <div class="contact" style="top:2661px">
    <svg width="16" height="18" viewBox="0 0 16 20"><path d="M8 0a7 7 0 0 0-7 7c0 5 7 13 7 13s7-8 7-13a7 7 0 0 0-7-7zm0 10a3 3 0 1 1 0-6 3 3 0 0 1 0 6z" fill="#3aae5c"/></svg>
    <span>248 Pueo Lane, Suite 310,<br>Honolulu, HI 96817</span>
  </div>
  <div class="contact" style="top:2719px">
    <svg width="16" height="16" viewBox="0 0 24 24"><path d="M6.6 10.8a15 15 0 0 0 6.6 6.6l2.2-2.2a1 1 0 0 1 1-.25 11 11 0 0 0 3.6.6 1 1 0 0 1 1 1V20a1 1 0 0 1-1 1A17 17 0 0 1 3 4a1 1 0 0 1 1-1h3.5a1 1 0 0 1 1 1c0 1.25.2 2.45.6 3.6a1 1 0 0 1-.25 1z" fill="#3aae5c"/></svg>
    <span>Phone: 808-555-0172</span>
  </div>
  <div class="contact" style="top:2753px">
    <svg width="16" height="14" viewBox="0 0 24 18"><path d="M0 0h24v18H0z" fill="#3aae5c"/><path d="M1 1l11 8 11-8" fill="none" stroke="#fff" stroke-width="2"/></svg>
    <span>info@marlowhealth-example.com</span>
  </div>

  <span class="social" style="left:524px"></span>
  <span class="social" style="left:567px"></span>
  <span class="social" style="left:606px"></span>
  <span class="social" style="left:645px"></span>

  <p class="copy">2024 Marlow Health Collective. All Rights Reserved.</p>
</footer>

</body>
</html>
```